Join Wait / Reservations Handout

This is a handout for guests with information about the ability to join our
waitlist and/or make reservations. It will be handed out to any guest that ends up waiting on our waitlist to be seated. It will describe how our waitlist and reservations system works. It is informational for them to download our mobile app.

It was forcing me to move the look and feel sliders. Please refer to our branding guide for look and feel.

Industry/Entity Type

Hospitality

Contact Information for Business Card

One of the attached documents give a very generic layout of the information we need on this card. This layout is more for where we wanted the information placed and has nothing to do with the design aspects of the piece. Please use your imagination. Any of the 5 colors in the branding guide can be used anywhere. The pineapple design can be used anywhere in any color combination.

If you require any other files please let me know. Thanks

Other font styles liked:
• Please see attached branding guide

Requirements
Must have
• The only color requirement is that the logo be the blue with teal lettering...This has to match our app store logo.

```html
<!DOCTYPE html>
<html lang="en">
<head>
<meta charset="utf-8">
<title>Join the Wait – Guest Handout</title>
<link rel="stylesheet" href="https://fonts.googleapis.com/css2?family=Jost:wght@700&family=Arimo:wght@400;700&display=swap">
<style>
  :root {
    --bg: #b9b9bc;
    --teal: #5c9b9c;
    --teal-light: #72b7b9;
    --navy: #06324a;
    --white: #ffffff;
    --icon-grey: #8a8a8a;
    --dash: #8f8f8f;
  }
  * { margin: 0; padding: 0; box-sizing: border-box; }
  html, body { width: 1146px; height: 1200px; overflow: hidden; }
  body { background: var(--bg); position: relative; }

  .card {
    position: absolute;
    top: 237px;
    width: 422px;
    height: 737px;
    text-align: center;
  }
  .card-front { left: 113px; background: var(--teal); color: var(--white); }
  .card-back  { left: 585px; background: var(--white); color: var(--navy); }

  .front-pattern {
    position: absolute; inset: 0;
    background: linear-gradient(135deg, #63a2a3 0%, #5a9899 50%, #63a2a3 100%);
  }
  .front-headline {
    position: absolute; top: 56px; left: 0; right: 0;
    font-family: "Jost", sans-serif; font-weight: 700;
    font-size: 28px; line-height: 48px; letter-spacing: 0.2px;
  }
  .brand-mark {
    position: absolute; left: 49px; top: 208px;
    width: 324px; height: 324px; border-radius: 50%;
    background: var(--navy);
    display: flex; align-items: center; justify-content: center;
  }
  .brand-name {
    font-family: "Arimo", sans-serif; font-weight: 700;
    font-size: 34px; line-height: 44px; color: var(--teal-light);
    letter-spacing: 1px;
  }
  .front-search {
    position: absolute; top: 594px; left: 0; right: 0;
    font-family: "Arimo", sans-serif; font-weight: 700;
    font-size: 22px; line-height: 36px;
  }

  .info {
    position: absolute; left: 0; right: 0;
  }
  .info-icon {
    display: block; margin: 0 auto;
    width: 58px; height: 58px;
  }
  .info-title {
    font-family: "Jost", sans-serif; font-weight: 700;
    font-size: 24px; line-height: 30px; letter-spacing: 0.3px;
  }
  .info-text {
    font-family: "Arimo", sans-serif; font-size: 19px; line-height: 24px;
  }
  .divider {
    position: absolute; left: 69px; width: 272px; height: 0;
    border-top: 1.5px dashed var(--dash);
  }
</style>
</head>
<body>

<section class="card card-front">
  <div class="front-pattern" role="img" aria-label="Geometric diamond pattern in teal tones"></div>
  <h1 class="front-headline">SAVE THE WAIT...<br>DOWNLOAD OUR APP</h1>
  <div class="brand-mark"><span class="brand-name">HARBOR<br>TABLE</span></div>
  <p class="front-search">SEARCH<br>“HARBOR TABLE BROOKFIELD”</p>
</section>

<section class="card card-back">
  <div class="info" style="top:25px">
    <svg class="info-icon" viewBox="0 0 58 58" fill="none" stroke="var(--icon-grey)" stroke-width="1.5">
      <circle cx="29" cy="29" r="28"/>
      <g stroke-linecap="round">
        <line x1="20" y1="19" x2="44" y2="19"/><line x1="20" y1="26" x2="44" y2="26"/>
        <line x1="20" y1="33" x2="44" y2="33"/><line x1="20" y1="40" x2="44" y2="40"/>
      </g>
      <g fill="var(--icon-grey)" stroke="none">
        <circle cx="15" cy="19" r="1.5"/><circle cx="15" cy="26" r="1.5"/>
        <circle cx="15" cy="33" r="1.5"/><circle cx="15" cy="40" r="1.5"/>
      </g>
    </svg>
    <h2 class="info-title" style="margin-top:12px">WHEN TO JOIN THE WAIT?</h2>
    <p class="info-text" style="margin-top:2px">Anytime</p>
  </div>
  <div class="divider" style="top:173px"></div>

  <div class="info" style="top:189px">
    <svg class="info-icon" viewBox="0 0 58 58" fill="none" stroke="var(--icon-grey)" stroke-width="1.5">
      <circle cx="29" cy="29" r="28"/>
      <rect x="14" y="14" width="30" height="29"/>
      <line x1="14" y1="19" x2="44" y2="19"/>
      <g stroke-width="1.2">
        <rect x="23" y="22" width="5" height="4"/><rect x="30" y="22" width="5" height="4"/><rect x="37" y="22" width="5" height="4"/>
        <rect x="16" y="29" width="5" height="4"/><rect x="23" y="29" width="5" height="4"/><rect x="30" y="29" width="5" height="4"/><rect x="37" y="29" width="5" height="4"/>
        <rect x="16" y="36" width="5" height="4"/><rect x="23" y="36" width="5" height="4"/><rect x="30" y="36" width="5" height="4"/>
      </g>
    </svg>
    <h2 class="info-title" style="margin-top:11px">WHEN TO RESERVE?</h2>
    <p class="info-text" style="margin-top:3px">Anytime - 2 Hours In Advance<br>(Excluding Weekends, Open-2pm)</p>
  </div>
  <div class="divider" style="top:362px"></div>

  <div class="info" style="top:379px">
    <svg class="info-icon" viewBox="0 0 58 58" fill="none" stroke="var(--icon-grey)" stroke-width="1.5">
      <circle cx="29" cy="29" r="28"/>
      <rect x="14" y="16" width="30" height="27" rx="2"/>
      <line x1="14" y1="22" x2="44" y2="22"/>
      <line x1="21" y1="12" x2="21" y2="18" stroke-width="2.5"/>
      <line x1="37" y1="12" x2="37" y2="18" stroke-width="2.5"/>
      <polyline points="21,32 27,38 38,26" stroke-width="2.5" stroke-linecap="round" stroke-linejoin="round"/>
    </svg>
    <h2 class="info-title" style="margin-top:8px;line-height:24px">SUNDAY<br><span style="font-size:20px;line-height:18px;display:block">+</span>HOLIDAY BUFFETS</h2>
    <p class="info-text" style="margin-top:0">(Coming June 2018)</p>
  </div>
  <div class="divider" style="top:553px"></div>

  <div class="info" style="top:571px">
    <svg class="info-icon" viewBox="0 0 58 58" fill="none" stroke="var(--icon-grey)" stroke-width="1.5">
      <circle cx="29" cy="29" r="28"/>
      <g fill="var(--icon-grey)" stroke="none">
        <circle cx="18" cy="22" r="5"/><circle cx="40" cy="22" r="5"/>
        <path d="M9 40 q0 -11 9 -11 q9 0 9 11 z"/><path d="M31 40 q0 -11 9 -11 q9 0 9 11 z"/>
        <circle cx="29" cy="21" r="6.5" stroke="var(--white)" stroke-width="1.5"/>
        <path d="M17 44 q0 -14 12 -14 q12 0 12 14 z" stroke="var(--white)" stroke-width="1.5"/>
      </g>
    </svg>
    <h2 class="info-title" style="margin-top:10px">LARGE GROUPS</h2>
    <p class="info-text" style="margin-top:0">Handled / Contacted<br>By Catering Manager</p>
  </div>
</section>

</body>
</html>
```